Wireless Internet Service Provider website design

We need a Internet Service Provider website that show the packages that we offer as well as the functionality where customers have the option of clicking on the various packages and be linked to a page where they can sign up for our services.
We need about 10-15 pages.
A. Integrated online store.
B. Live chat.
C. Social media page
My old website. Brightlinkradio.nyc

Example: http://plumcrestnet.com/services/residential/ Added Tuesday, June 7, 2016

Target Market(s)

Residential and small businesses

Industry/Entity Type

Internet

Coding

Coded - Design and coding required

Number of Pages Required

5+ page

Font styles to use
Serif
Sans Serif
Script

Colors
3176b5
85cae6
ffffff

Requirements
Must have
• Online store and live chat, drop down details on pricing from current website
Nice to have
• great design, functional website,

```html
<!DOCTYPE html>
<html lang="en">
<head>
<meta charset="utf-8">
<title>Quillmere Wireless — Wireless Internet</title>
<link href="https://fonts.googleapis.com/css2?family=Lato:wght@300;400;700&family=Open+Sans:wght@400;600;700&display=swap" rel="stylesheet">
<style>
:root{
  --blue:#0b5fa5;
  --blue-deep:#0a3f78;
  --navy:#0d2a4c;
  --sky:#85cae6;
  --teal:#1a9fc9;
  --grey-bg:#efefef;
  --text:#333;
  --muted:#666;
  --white:#fff;
}
*{box-sizing:border-box;margin:0;padding:0}
html,body{width:1200px;height:3689px;overflow:hidden}
body{font-family:"Open Sans",Arial,sans-serif;color:var(--text);background:var(--white);position:relative}
.abs{position:absolute}
/* top bar */
.topbar{position:absolute;top:0;left:0;width:1200px;height:48px;border-bottom:1px solid #e4e4e4;font-size:13px;color:#555}
.topbar .connect{left:145px;top:15px;display:flex;align-items:center;gap:8px}
.dot{width:10px;height:10px;border-radius:50%;background:#555;display:inline-block}
.topbar .phone{left:668px;top:15px;display:flex;gap:6px;align-items:center}
.topbar .cart{left:822px;top:15px;display:flex;gap:6px;align-items:center}
.livechat{left:940px;top:9px;background:var(--blue);color:#fff;font-weight:700;font-size:12px;border-radius:14px;padding:6px 18px}
/* nav */
.logo{font-family:"Open Sans",Arial,sans-serif;font-weight:700;font-size:24px;color:var(--navy);display:flex;align-items:center;gap:10px}
.logo .mark{width:18px;height:18px;border-radius:50%;background:var(--blue)}
.nav-logo{left:148px;top:66px}
.menu{left:522px;top:88px;display:flex;gap:28px;font-size:12px;color:#333}
.menu .active{color:var(--blue)}
/* hero */
.hero{left:0;top:135px;width:1200px;height:468px;background:linear-gradient(90deg,#6e6760 0%,#b9b3ad 25%,#e7e8ea 50%,#eef0f3 100%)}
.hero h1{position:absolute;left:676px;top:126px;font-family:Lato,sans-serif;font-weight:400;font-size:31px;line-height:38px;color:var(--blue-deep)}
.hero p{position:absolute;left:676px;top:222px;width:410px;font-size:14px;line-height:24px;color:#444}
.btn{display:inline-block;background:var(--navy);color:#fff;font-size:12px;border-radius:16px;padding:9px 28px;text-transform:uppercase}
.hero .btn{position:absolute;left:682px;top:312px;padding:11px 32px}
.dots{position:absolute;left:1168px;top:345px;display:flex;flex-direction:column;gap:14px}
.dots span{width:9px;height:9px;border-radius:50%;background:#c9ccd0}
.dots span:first-child{background:var(--blue-deep)}
/* section titles */
.title{position:absolute;left:0;width:1200px;text-align:center;font-family:Lato,sans-serif;font-weight:400;font-size:37px}
/* provide cards */
.card{position:absolute;top:760px;width:443px;height:551px;background:var(--blue)}
.card .photo{height:273px;background:linear-gradient(135deg,#c8a985,#e8dccd 60%,#9a8a78)}
.card h3{margin:26px 0 0 22px;font-family:Lato,sans-serif;font-weight:400;font-size:30px;line-height:36px;color:#fff}
.card h3 b{color:var(--sky);font-weight:400}
.card p{margin:14px 22px 0;font-size:13px;line-height:22px;color:#fff}
.card .btn{margin:24px 0 0 22px;padding:7px 16px;font-size:12px}
/* store */
.store{left:0;top:1367px;width:1200px;height:615px;background:var(--grey-bg)}
.rule{position:absolute;left:145px;top:126px;width:910px;height:1px;background:#c9c9c9}
.product{position:absolute;top:153px;width:285px;text-align:center}
.product .photo{height:196px;background:linear-gradient(135deg,#d9d9d9,#f5f5f5 60%,#b0b5ba)}
.product h4{margin-top:34px;font-size:18px;font-weight:400;color:var(--blue)}
.product p{margin-top:18px;font-size:14px;line-height:24px;color:#444}
.product .btn{margin-top:22px;background:var(--blue);padding:9px 22px}
/* plans */
.plans{left:0;top:1982px;width:1200px;height:802px;background:linear-gradient(180deg,#1c1c1c,#3b3b3b 50%,#202020)}
.plan{position:absolute;top:195px;width:221px;height:503px;background:linear-gradient(180deg,#fff,#dcdcdc);text-align:center;border:1px solid #ccc}
.plan .head{height:110px;background:var(--navy);color:#fff;padding-top:22px}
.plan .price{font-size:37px;font-weight:400}
.plan .cycle{font-size:11px;letter-spacing:.5px}
.plan h5{margin-top:24px;font-size:25px;line-height:28px;color:var(--blue);font-weight:600}
.plan .speed{margin-top:16px;font-size:23px;color:#333}
.plan .sub{font-size:11px;color:var(--blue)}
.plan .desc{margin:16px 18px 0;font-size:10px;line-height:16px;color:#444}
.plan ul{list-style:none;text-align:left;margin:14px 0 0 32px;font-size:11px;color:#444}
.plan li{display:flex;align-items:center;gap:10px;height:24px}
.plan .btn{margin-top:18px;background:var(--navy);padding:8px 0;width:180px;font-size:11px}
.plan.featured{top:170px;height:553px}
.plan.featured .head{height:135px;padding-top:46px;background:linear-gradient(180deg,#0e7fb0,var(--teal))}
.plan.featured .btn{background:var(--teal)}
/* testimonials */
.testi{left:0;top:2784px;width:1200px;height:475px;background:var(--blue)}
.avatar{position:absolute;top:192px;width:147px;height:147px;border-radius:50%;border:5px solid var(--sky);background:linear-gradient(135deg,#8aa0b3,#d7dde2)}
.quote{position:absolute;top:130px;width:290px;color:#fff;font-size:14px;line-height:24px}
.quote .mark{font-family:Lato,serif;font-size:54px;line-height:40px;font-weight:700}
.quote hr{border:0;border-top:1px solid rgba(255,255,255,.7);margin-top:28px;width:290px}
.name{position:absolute;top:384px;color:#fff;font-size:23px;font-family:Lato,sans-serif}
/* footer */
.footer{left:0;top:3259px;width:1200px;height:356px;background:#f4f4f4}
.feature{position:absolute;top:36px;display:flex;gap:14px;align-items:center;font-size:14px;color:var(--blue);line-height:17px}
.fcol{position:absolute;top:140px;font-size:13px;line-height:27px;color:#333}
.fcol h6{font-size:13px;font-weight:700;color:var(--blue);margin-bottom:14px;line-height:27px;text-transform:uppercase}
.bottombar{left:0;top:3615px;width:1200px;height:74px;border-top:1px solid #ddd;font-size:13px;color:#444}
</style>
</head>
<body>

<header class="topbar">
  <div class="abs connect">Connect With Us :
    <span class="dot"></span><span class="dot"></span><span class="dot"></span><span class="dot"></span>
    <span style="color:#ccc">|</span>
    <svg width="14" height="14" viewBox="0 0 14 14"><circle cx="6" cy="6" r="4.5" fill="none" stroke="#1a9fc9" stroke-width="1.6"/><line x1="9.3" y1="9.3" x2="13" y2="13" stroke="#1a9fc9" stroke-width="1.8"/></svg>
  </div>
  <div class="abs phone"><svg width="12" height="12" viewBox="0 0 12 12"><path d="M2 1l2 0 1 3-1.5 1a7 7 0 0 0 3.5 3.5L8 7l3 1 0 2c0 1-1 1-1 1A9 9 0 0 1 1 2S1 1 2 1z" fill="#1a9fc9"/></svg>(866) 555-0142</div>
  <div class="abs cart"><svg width="18" height="16" viewBox="0 0 18 16"><path d="M1 2h3l2 8h9l2-6H5" fill="none" stroke="#444" stroke-width="1.5"/><circle cx="7" cy="13.5" r="1.5" fill="#444"/><circle cx="14" cy="13.5" r="1.5" fill="#444"/></svg>Cart (0 Items)</div>
  <div class="abs livechat">LIVE CHAT</div>
</header>

<nav>
  <div class="abs logo nav-logo"><span class="mark"></span>Quillmere Wireless</div>
  <svg class="abs" style="left:533px;top:66px" width="18" height="10" viewBox="0 0 18 10"><path d="M1 1l8 7 8-7" fill="none" stroke="#0b5fa5" stroke-width="2"/></svg>
  <div class="abs menu"><span class="active">HOME</span><span>WHY QUILLMERE</span><span>PLANS &amp; PACKAGES</span><span>MY ACCOUNT</span><span>GALLERY</span><span>CONTACTS</span></div>
</nav>

<section class="abs hero">
  <div class="abs" role="img" aria-label="Hand holding a glowing globe with network lines" style="left:0;top:0;width:620px;height:468px;background:radial-gradient(circle at 230px 160px,#c9cfd6 0,#8d9aa6 90px,transparent 170px)"></div>
  <h1>LOCALLY OWN.RELIABLE<br>SUPER FAST INTERNET .</h1>
  <p>Welcome to Quillmere's fiber-speed network without fiber – the new choice for those of you who don't feel you have a lot of choices.</p>
  <span class="btn">Learn More</span>
  <div class="dots"><span></span><span></span><span></span></div>
</section>

<h2 class="title" style="top:665px">WHAT WE PROVIDE ?</h2>
<article class="card" style="left:145px">
  <div class="photo" role="img" aria-label="Smiling man working on a laptop at home"></div>
  <h3><b>RESIDENTIAL</b><br>INTERNET PLAN</h3>
  <p>Lorem ipsum dolor sit amet, consectetur adipiscing elit, sed do eiusmod tempor incididunt ut labore et dolore magna aliqua. Ut enim ad minim veniam, quis nostrud exercitation ullamco laboris nisi ut aliquip</p>
  <span class="btn">Learn More</span>
</article>
<article class="card" style="left:612px">
  <div class="photo" role="img" aria-label="Business team meeting around a table" style="background:linear-gradient(135deg,#9a8f86,#e9e6e2 55%,#6f6a66)"></div>
  <h3><b>BUSINESS</b><br>INTERNET PLAN</h3>
  <p>Lorem ipsum dolor sit amet, consectetur adipiscing elit, sed do eiusmod tempor incididunt ut labore et dolore magna aliqua. Ut enim ad minim veniam, quis nostrud exercitation ullamco laboris nisi ut aliquip</p>
  <span class="btn">Learn More</span>
</article>

<section class="abs store">
  <h2 class="title" style="top:50px;color:var(--blue)">ONLINE STORE</h2>
  <div class="rule"></div>
  <div class="product" style="left:145px"><div class="photo" role="img" aria-label="Portable wireless hotspot device"></div><h4>QUILLMERE WIRELESS</h4><p>Lorem ipsum dolor sit amet, consectetur<br>adipiscing elit, sed do eiusmod</p><span class="btn">Add to Cart</span></div>
  <div class="product" style="left:457px"><div class="photo" role="img" aria-label="Hands holding a tablet"></div><h4>QUILLMERE WIRELESS</h4><p>Lorem ipsum dolor sit amet, consectetur<br>adipiscing elit, sed do eiusmod</p><span class="btn">Add to Cart</span></div>
  <div class="product" style="left:767px"><div class="photo" role="img" aria-label="Wireless router on a desk"></div><h4>QUILLMERE WIRELESS</h4><p>Lorem ipsum dolor sit amet, consectetur<br>adipiscing elit, sed do eiusmod</p><span class="btn">Add to Cart</span></div>
</section>

<section class="abs plans" role="img" aria-label="Dark background photo of hands on a laptop">
  <h2 class="title" style="top:80px;color:#fff">OUR PLANS</h2>
  <div class="plan" style="left:160px"><div class="head"><div class="price">$39.99</div><div class="cycle">MONTHLY/1YR</div></div><h5>Quillmere<br>Simplicity</h5><div class="speed">5 Mbps</div><div class="sub">Download Speed</div><p class="desc">The right speed for occasional internet usage, including checking emails, social networks and light internet browsing.</p><ul><li>✔ Free smart router</li><li>✔ Free internet protection</li><li>✔ Unlimited Quillmere</li><li>✔ Wi-Fi access</li></ul><span class="btn">Try It Now</span></div>
  <div class="plan" style="left:381px"><div class="head"><div class="price">$39.99</div><div class="cycle">MONTHLY/1YR</div></div><h5>Quillmere<br>Simplicity</h5><div class="speed">10 Mbps</div><div class="sub">Download Speed</div><p class="desc">The right speed for occasional internet usage, including checking emails, social networks and light internet browsing.</p><ul><li>✔ Free smart router</li><li>✔ Free internet protection</li><li>✔ Unlimited Quillmere</li><li>✔ Wi-Fi access</li></ul><span class="btn">Try It Now</span></div>
  <div class="plan featured" style="left:602px"><div class="head"><div class="price">$39.99</div><div class="cycle">MONTHLY/1YR</div></div><h5>Quillmere<br>Simplicity</h5><div class="speed">50 Mbps</div><div class="sub">Download Speed</div><p class="desc">The right speed for occasional internet usage, including checking emails, social networks and light internet browsing.</p><ul><li>✔ Free smart router</li><li>✔ Free internet protection</li><li>✔ Unlimited Quillmere</li><li>✔ Wi-Fi access</li></ul><span class="btn">Try It Now</span></div>
  <div class="plan" style="left:821px"><div class="head"><div class="price">$39.99</div><div class="cycle">MONTHLY/1YR</div></div><h5>Quillmere<br>Simplicity</h5><div class="speed">25 Mbps</div><div class="sub">Download Speed</div><p class="desc">The right speed for occasional internet usage, including checking emails, social networks and light internet browsing.</p><ul><li>✔ Free smart router</li><li>✔ Free internet protection</li><li>✔ Unlimited Quillmere</li><li>✔ Wi-Fi access</li></ul><span class="btn">Try It Now</span></div>
</section>

<section class="abs testi">
  <h2 class="title" style="top:80px;color:#fff">TESTIMONIALS</h2>
  <svg class="abs" style="left:50px;top:240px" width="16" height="26" viewBox="0 0 16 26"><path d="M13 2L3 13l10 11" fill="none" stroke="#fff" stroke-width="3"/></svg>
  <svg class="abs" style="left:1132px;top:240px" width="16" height="26" viewBox="0 0 16 26"><path d="M3 2l10 11-10 11" fill="none" stroke="#fff" stroke-width="3"/></svg>
  <div class="avatar" style="left:148px" role="img" aria-label="Customer portrait"></div>
  <div class="quote" style="left:310px"><div class="mark">“</div>Thanks for your great service. I love my internet and your quick response to my questions and concerns. I would definitely refer Quillmere to my friends and family. Keep up the good<hr></div>
  <div class="name" style="left:312px">Mark Ellison</div>
  <div class="avatar" style="left:614px" role="img" aria-label="Customer portrait"></div>
  <div class="quote" style="left:776px"><div class="mark">“</div>Thanks for your great service. I love my internet and your quick response to my questions and concerns. I would definitely refer Quillmere to my friends and family. Keep up the good<hr></div>
  <div class="name" style="left:772px">Daniel Reyes</div>
</section>

<footer class="abs footer">
  <div class="abs logo" style="left:145px;top:42px"><span class="mark"></span>Quillmere Wireless</div>
  <div class="feature" style="left:525px"><svg width="30" height="26" viewBox="0 0 30 26"><path d="M3 3h24v14H13l-6 6v-6H3z" fill="none" stroke="#0b5fa5" stroke-width="2.4"/></svg>Customer<br>Support Centre</div>
  <div class="feature" style="left:718px"><svg width="28" height="28" viewBox="0 0 28 28"><circle cx="14" cy="14" r="9" fill="none" stroke="#0b5fa5" stroke-width="5" stroke-dasharray="4 3"/><circle cx="14" cy="14" r="4" fill="#0b5fa5"/></svg>Equipment<br>Options</div>
  <div class="feature" style="left:912px"><svg width="26" height="28" viewBox="0 0 26 28"><circle cx="13" cy="8" r="6" fill="#0b5fa5"/><path d="M2 27a11 11 0 0 1 22 0z" fill="#0b5fa5"/></svg>Customer<br>Guarantee</div>
  <div class="fcol" style="left:145px"><h6>Quick Links</h6>Refer a Friend<br>Free Internet for life<br>Terms &amp; Conditions<br>Privacy Policy<br>Site Map</div>
  <div class="fcol" style="left:323px;top:181px">Wireless Internet Access Agreement<br>Quillmere Internet Access<br>Customer Support Center<br>Catalog</div>
  <div class="fcol" style="left:608px"><h6>Contact Us</h6>418 Marlow Street | 2nd Fl<br>Brooklyn, NY 11201<br>Phone:&nbsp; 866-555-0142</div>
  <div class="fcol" style="left:815px"><h6>Email &amp; Web</h6>Emails:&nbsp; support@brightlinkradio.nyc<br><span style="padding-left:56px">sale@brightlinkradio.nyc</span><br>Web address:&nbsp; brightlinkradio.nyc</div>
</footer>

<div class="abs bottombar">
  <div class="abs" style="left:145px;top:27px">Brightlinkradio.nyc © 2016 &nbsp;|&nbsp; All Rights Reserved</div>
  <div class="abs" style="left:864px;top:27px">Privacy Policy &nbsp;|&nbsp; Terms Of Use</div>
</div>

</body>
</html>
```